App design for timesheet system (desgn in Figma)

I am currently looking for a designer to design an app for my company. I run a labour hire/recruitment company and the app submits timesheets/timecards on a weekly basis.

PLEASE USE MY CURRENT THEME. I WOULD ONLY LIKE SUBMISSIONS USING MY THEME OF THE RED TRIANGLES/GRAY TRIANGLES. USE MY COLOURS.

(PAGE 1)
Loading/Landing page, logo with my theme incorporated in the page (AS PER ATTACHMENT)

(PAGE 2)
A dynamic changing page. This page changes according to the submissions (all of these are required for development). Using MY THEME, the functionality will be as follows:
- Ability to add companies and link different jobsites to them (sprites for adding company).
- The third page lists all the companies with jobsites as drop down. This must also have a 'calendar' (pn the top) or some sort of form where you can change the week you are submitting the timesheets for. We usually go by the Sunday and refer to it as WE (Week Ending).

(PAGE 3)
- When you tap on a jobsite, take you to a new page where you can attach multiple photos from your photo library. Ability to also write notes. The photos and notes save automatically when added, then a button to 'Send' which;
- Sends photos attached to an email to our TIMESHEETS email.
- The email subject will be '[COMPANY] - [JOBSITE] - [WE DATE]' and the body of the email will have [NOTES].
- Once a timesheet is submitted, a checkmark is added next to the jobsite for that week. (BACK TO PAGE 2, ADDING CHECKMARK)
- Able to send photos from photo library, messages or chirpbox directly to the app under 'share'. Once the app is tapped from share photo, it will take you to the 'allocation' page where all the companies and jobsites are and you choose the jobsite to allocate to. This will not send to email yet but rather save in the app.

To simply,
1. Landing Page (loading)
2. Companies/jobsites page
- Add (DD.MM.YY - DD.MM.YY) to the top to signify the week we are referring to. This could be beside the calendar.
- Each rectangle below the dates should have "COMPANY NAME", this is a rectangle that will be a drop-down to display different jobsites.
- The jobsites will be 'sub-menus' so indent them a little.
- There are no buttons on this page.
- The 'jobsites' sub-menu will take you to the 3rd page
- There should be 'ticks' similar to Quillnote ticks for 'delivered, sent, seen'.
- These ticks will be '1. Photos Attached, 2. Submitted Timesheets, 3. Timesheets Sent'
3. Timesheet submission
- This page will be where the photos are submitted.
- At the top, there should be a button that says 'SUBMITTED TIMESHEETS' this will take you to the 4th page.
- Form for 'ATTACH FILE' (UPLOAD)
- Form for Notes
- Button to 'SUBMIT'
- The submit button will then go to the 4th page.
4. Timesheet display & Send
- The submitted timesheets are in rectangle and should be displayed in a matter of '1. COMPANY-JOBSITE', '2. COMPANY-JOBSITE'
- Similar to the dropdown boxes from page 2, these rectangles should have a dropdown and display the timesheet preview. When tapped on, the timesheet will expand in view.
- This page should have a "SUBMIT TIMESHEETS' button which will:
- Submit the timesheets, this will be sent to an email as described in the brief above.

```html
<!DOCTYPE html>
<html lang="en">
<head>
<meta charset="utf-8">
<title>Keystone Crew – Timesheet App Screens</title>
<link rel="stylesheet" href="https://fonts.googleapis.com/css2?family=Heebo:wght@300;400;500;700&family=Barlow+Semi+Condensed:wght@500;600;700&display=swap">
<style>
  :root{
    --canvas:#dde4ec;
    --red-deep:#6a1a22;
    --red:#8c1b22;
    --red-bright:#b0202a;
    --red-badge:#e0222b;
    --white:#ffffff;
    --grey-bar:#e4e6ea;
    --grey-line:#d6d8dc;
    --ink:#2a2a2a;
    --ink-soft:#3c3c3c;
    --dark-btn:#2b2b2d;
    --teal:#2aa58f;
    --tick-grey:#a8a8a8;
    --track:#c89a9d;
  }
  *{box-sizing:border-box;margin:0;padding:0}
  html,body{width:1200px;height:799px;overflow:hidden;background:var(--canvas);font-family:"Heebo",sans-serif}
  .stage{position:relative;width:1200px;height:799px}
  .screen{position:absolute;top:88px;width:278px;height:600px;border-radius:30px;overflow:hidden}
  .screen--loading{left:107px;background:var(--red-deep)}
  .screen--companies{left:457px;background:var(--red)}
  .screen--jobsite{left:807px;background:var(--red)}
  .backdrop{position:absolute;inset:0}
  .screen--loading .backdrop{background:linear-gradient(160deg,#7a2129 0%,#6a1a22 45%,#5a141b 100%)}
  .screen--companies .backdrop{background:linear-gradient(170deg,#9a1f27 0%,#8a1a21 60%,#7c171e 100%)}
  .screen--jobsite .backdrop{background:linear-gradient(165deg,#8f1c23 0%,#a11f28 45%,#7a161d 100%)}

  .brand-ghost{position:absolute;left:28px;top:54px;font:700 40px/1 "Heebo",sans-serif;color:rgba(0,0,0,.18);letter-spacing:-1px}
  .loader{position:absolute;inset:0}
  .loading-label{position:absolute;left:0;right:0;top:354px;text-align:center;font:300 30px/1 "Heebo",sans-serif;color:var(--white)}
  .progress{position:absolute;left:33px;top:508px;width:210px;height:15px;border-radius:8px;background:var(--track);overflow:hidden}
  .progress__fill{width:121px;height:100%;background:#f4eeee;border-radius:8px}

  .topbar{position:absolute;left:0;right:0;top:0;height:80px}
  .icon-btn{position:absolute;top:22px;width:20px;height:20px}
  .icon-btn--back{left:16px}
  .icon-btn--search{right:16px}
  .brand{position:absolute;left:0;right:0;text-align:center;font:700 22px/1 "Heebo",sans-serif;color:var(--white);letter-spacing:-.5px}
  .topbar .brand{top:36px}

  .week{position:absolute;left:7px;right:6px;top:82px;background:var(--white);display:grid;grid-template-columns:repeat(7,1fr)}
  .week__day{height:29px;display:flex;align-items:center;justify-content:center;font:500 9px/1 "Heebo",sans-serif;color:var(--ink-soft);border-right:1px solid var(--grey-line);border-bottom:1px solid var(--grey-line)}
  .week__date{height:36px;display:flex;align-items:center;justify-content:center;font:500 12px/1 "Heebo",sans-serif;color:var(--ink);border-right:1px solid var(--grey-line)}
  .week__day:nth-child(7),.week__date:nth-child(14){border-right:0}
  .week__date--current span{width:18px;height:18px;border-radius:50%;background:var(--red-badge);color:var(--white);display:flex;align-items:center;justify-content:center;font-size:11px}

  .company-select{position:absolute;left:0;right:0;top:159px;height:44px;background:var(--grey-bar);display:flex;align-items:center;justify-content:space-between;padding:0 14px 0 14px;font:500 12.5px/1 "Heebo",sans-serif;color:var(--ink-soft);letter-spacing:.2px}

  .jobsite-card{position:absolute;left:7px;width:265px;height:116px;background:var(--white)}
  .jobsite-card:nth-of-type(1){top:216px}
  .jobsite-card:nth-of-type(2){top:343px}
  .jobsite-card:nth-of-type(3){top:470px}
  .jobsite-card__mark{position:absolute;left:8px;top:8px;width:93px;height:100px;border:1px solid #e5e5e5;display:flex;flex-direction:column;align-items:center;justify-content:center;gap:8px}
  .mark-square{width:26px;height:26px;background:#d9dde2}
  .mark-name{font:500 9px/1 "Heebo",sans-serif;color:var(--ink-soft);letter-spacing:.3px}
  .jobsite-card__title{position:absolute;left:120px;top:15px;font:400 12.5px/1 "Heebo",sans-serif;color:var(--ink)}
  .jobsite-card__text{position:absolute;left:120px;top:34px;width:135px;font:400 11px/16px "Heebo",sans-serif;color:var(--ink-soft)}
  .jobsite-card__tick{position:absolute;left:234px;top:11px;width:16px;height:12px}
  .add-btn{position:absolute;left:120px;top:76px;height:24px;padding:0 9px;border:1.5px solid var(--red);border-radius:3px;display:flex;align-items:center;gap:4px;font:700 8.5px/1 "Barlow Semi Condensed",sans-serif;color:var(--red);letter-spacing:.3px;font-family:"Heebo",sans-serif}

  .jobsite-brand{top:140px;font-size:25px}
  .jobsite-title{position:absolute;left:0;right:0;top:192px;text-align:center;font:700 23px/1 "Barlow Semi Condensed",sans-serif;color:var(--white);letter-spacing:.5px}
  .btn-secondary{position:absolute;left:22px;width:235px;top:236px;height:42px;background:#e6e6e6;display:flex;align-items:center;justify-content:center;font:600 13.5px/1 "Barlow Semi Condensed",sans-serif;color:var(--ink-soft);letter-spacing:.6px}
  .field{position:absolute;left:22px;width:235px;height:42px;background:var(--white);display:flex;align-items:center;justify-content:space-between;padding:0 6px 0 21px;font:400 13px/1 "Heebo",sans-serif;color:var(--ink-soft)}
  .field--file{top:296px}
  .field--notes{top:356px}
  .upload-icon{width:29px;height:29px;border-radius:50%;background:var(--red);display:flex;align-items:center;justify-content:center}
  .btn-primary{position:absolute;left:22px;width:236px;top:414px;height:44px;background:var(--dark-btn);display:flex;align-items:center;justify-content:center;font:700 14.5px/1 "Barlow Semi Condensed",sans-serif;color:var(--white);letter-spacing:.5px}
</style>
</head>
<body>
<main class="stage">

  <section class="screen screen--loading" aria-label="Loading screen">
    <div class="backdrop" role="img" aria-label="Dark red backdrop with a faint construction site and worker in a hard hat"></div>
    <div class="brand-ghost" aria-hidden="true">Keystone Crew</div>
    <svg class="loader" viewBox="0 0 278 600" aria-hidden="true">
      <g fill="#fff">
        <circle cx="143" cy="164" r="22"/>
        <circle cx="88" cy="186" r="20"/>
        <circle cx="66" cy="241" r="18"/>
        <circle cx="88" cy="296" r="16"/>
        <circle cx="143" cy="319" r="13"/>
        <circle cx="197" cy="297" r="11"/>
        <circle cx="220" cy="241" r="9"/>
        <circle cx="197" cy="186" r="7"/>
      </g>
    </svg>
    <p class="loading-label">Loading</p>
    <div class="progress"><div class="progress__fill"></div></div>
  </section>

  <section class="screen screen--companies" aria-label="Companies and jobsites">
    <div class="backdrop"></div>
    <header class="topbar">
      <svg class="icon-btn icon-btn--back" viewBox="0 0 20 20" aria-label="Back"><path d="M10 3 3 10l7 7M3 10h15" fill="none" stroke="#fff" stroke-width="3" stroke-linejoin="round"/></svg>
      <div class="brand">Keystone Crew</div>
      <svg class="icon-btn icon-btn--search" viewBox="0 0 20 20" aria-label="Search"><circle cx="8.5" cy="8.5" r="5.5" fill="none" stroke="#fff" stroke-width="2.6"/><path d="m13 13 4.5 4.5" stroke="#fff" stroke-width="3" stroke-linecap="round"/></svg>
    </header>

    <div class="week">
      <div class="week__day">SUN</div><div class="week__day">MON</div><div class="week__day">TUE</div><div class="week__day">WED</div><div class="week__day">THUR</div><div class="week__day">FRI</div><div class="week__day">SAT</div>
      <div class="week__date">1</div><div class="week__date week__date--current"><span>2</span></div><div class="week__date">3</div><div class="week__date">4</div><div class="week__date">5</div><div class="week__date">6</div><div class="week__date">7</div>
    </div>

    <div class="company-select">COMPANY NAME
      <svg width="12" height="8" viewBox="0 0 12 8" aria-hidden="true"><path d="m1 1 5 5 5-5" fill="none" stroke="#3c3c3c" stroke-width="1.6"/></svg>
    </div>

    <article class="jobsite-card">
      <div class="jobsite-card__mark"><span class="mark-square"></span><span class="mark-name">COMPANY NAME</span></div>
      <h3 class="jobsite-card__title">Nemo enim ipsam</h3>
      <p class="jobsite-card__text">Sed ut perspiciatis unde omnis iste natus</p>
      <svg class="jobsite-card__tick" viewBox="0 0 16 12" aria-label="Not submitted"><path d="M1 6.5 4.5 10 11 2M7 9l1 1 7-8" fill="none" stroke="var(--tick-grey)" stroke-width="1.8"/></svg>
      <div class="add-btn"><svg width="8" height="8" viewBox="0 0 8 8"><path d="M4 0v8M0 4h8" stroke="var(--red)" stroke-width="2"/></svg>ADD COMPANIES</div>
    </article>

    <article class="jobsite-card">
      <div class="jobsite-card__mark"><span class="mark-square"></span><span class="mark-name">Harbor Lane</span></div>
      <h3 class="jobsite-card__title">Nemo enim ipsam</h3>
      <p class="jobsite-card__text">Sed ut perspiciatis unde omnis iste natus</p>
      <svg class="jobsite-card__tick" viewBox="0 0 16 12" aria-label="Submitted"><path d="M1 6.5 4.5 10 11 2M7 9l1 1 7-8" fill="none" stroke="var(--teal)" stroke-width="1.8"/></svg>
      <div class="add-btn"><svg width="8" height="8" viewBox="0 0 8 8"><path d="M4 0v8M0 4h8" stroke="var(--red)" stroke-width="2"/></svg>ADD COMPANIES</div>
    </article>

    <article class="jobsite-card">
      <div class="jobsite-card__mark"><span class="mark-square"></span><span class="mark-name">Orbitra</span></div>
      <h3 class="jobsite-card__title">Nemo enim ipsam</h3>
      <p class="jobsite-card__text">Sed ut perspiciatis unde omnis iste natus</p>
      <svg class="jobsite-card__tick" viewBox="0 0 16 12" aria-label="Not submitted"><path d="M1 6.5 4.5 10 11 2M7 9l1 1 7-8" fill="none" stroke="var(--tick-grey)" stroke-width="1.8"/></svg>
      <div class="add-btn"><svg width="8" height="8" viewBox="0 0 8 8"><path d="M4 0v8M0 4h8" stroke="var(--red)" stroke-width="2"/></svg>ADD COMPANIES</div>
    </article>
  </section>

  <section class="screen screen--jobsite" aria-label="Jobsite timesheet submission">
    <div class="backdrop" role="img" aria-label="Red backdrop with a faint building under construction and scaffolding"></div>
    <header class="topbar">
      <svg class="icon-btn icon-btn--back" viewBox="0 0 20 20" aria-label="Back"><path d="M10 3 3 10l7 7M3 10h15" fill="none" stroke="#fff" stroke-width="3" stroke-linejoin="round"/></svg>
      <svg class="icon-btn icon-btn--search" viewBox="0 0 20 20" aria-label="Search"><circle cx="8.5" cy="8.5" r="5.5" fill="none" stroke="#fff" stroke-width="2.6"/><path d="m13 13 4.5 4.5" stroke="#fff" stroke-width="3" stroke-linecap="round"/></svg>
    </header>
    <div class="brand jobsite-brand">Keystone Crew</div>
    <h2 class="jobsite-title">JOBSITE</h2>
    <div class="btn-secondary">SUBMITTED TIMESHEETS</div>
    <div class="field field--file">Attach File
      <span class="upload-icon"><svg width="14" height="14" viewBox="0 0 14 14" aria-hidden="true"><path d="M7 10V2M3.5 5.5 7 2l3.5 3.5" fill="none" stroke="#fff" stroke-width="2"/><path d="M1 9v4h12V9" fill="none" stroke="#fff" stroke-width="2"/></svg></span>
    </div>
    <div class="field field--notes">Notes</div>
    <div class="btn-primary">SUBMIT</div>
  </section>

</main>
</body>
</html>
```